Harbor Law Stationary - Law Firm

I am looking for a designer who can help me design letterhead and envelopes consistent with our new business cards. Feel free to reach out to me directly at ned@harborlawgroup.example. Thank you!! Visit harborlawgroup.example to see our site and the attached files for creative assets.

Target Market(s)

Anyone needing a lawyer

Font styles to use
Other font styles liked:
• Adobe Caslon Pro

Requirements
Must have
• Adobe Caslon Pro font
Full color
Nice to have
• My photo on front along with 2/3 face of camo - see mock up for example of what I have in mind.

American colors - similar to the ones found on my website and gold.

```html
<!DOCTYPE html>
<html lang="en">
<head>
<meta charset="utf-8">
<title>Harbor Law Stationery</title>
<link rel="stylesheet" href="https://fonts.googleapis.com/css2?family=Libre+Caslon+Text:wght@400;700&family=Arimo:wght@400&display=swap">
<style>
  :root {
    --backdrop: #7a7879;
    --navy: #0a2748;
    --gold: #a99a5c;
    --gold-text: #b9a66a;
    --paper: #ffffff;
    --ink: #4a4a4a;
    --ink-dark: #2a3344;
    --faint: #f2f0ea;
  }
  * { margin: 0; padding: 0; box-sizing: border-box; }
  html, body { width: 1200px; height: 770px; overflow: hidden; }
  body { background: var(--backdrop); position: relative; font-family: "Arimo", Arial, sans-serif; }

  .sheet { position: absolute; background: var(--paper); box-shadow: 0 2px 6px rgba(0,0,0,.35); overflow: hidden; }
  .sheet > svg.art { position: absolute; inset: 0; width: 100%; height: 100%; }

  .letterhead { left: 93px; top: 63px; width: 457px; height: 643px; }
  .brand { position: absolute; display: flex; align-items: center; gap: 8px;
    font-family: "Libre Caslon Text", Georgia, serif; font-weight: 700; color: var(--gold-text);
    font-size: 15px; letter-spacing: .8px; text-transform: uppercase; }
  .brand-dot { width: 14px; height: 14px; border-radius: 50%; background: var(--gold-text); }
  .letterhead .brand { left: 50px; top: 30px; }

  .contact { position: absolute; left: 321px; top: 12px; font-family: "Libre Caslon Text", Georgia, serif;
    color: #fff; font-size: 7.6px; line-height: 9.6px; }
  .contact .gap { height: 4px; }
  .contact .row { display: flex; align-items: center; gap: 4px; }
  .contact svg { width: 7px; height: 7px; fill: var(--gold-text); }

  .letter { position: absolute; left: 48px; top: 246px; width: 360px; color: var(--ink); }
  .salutation { font-size: 9.4px; margin-bottom: 10px; }
  .letter p.body { font-size: 7px; line-height: 10.8px; text-align: justify; margin-bottom: 10.8px; }
  .closing { position: absolute; left: 48px; top: 463px; font-size: 7.4px; color: var(--ink); }
  .signature { position: absolute; left: 48px; top: 490px; width: 58px; height: 22px; background: linear-gradient(90deg, #e6e8ec, #f4f5f7); }

  .services { position: absolute; left: 48px; top: 595px; font-family: "Libre Caslon Text", Georgia, serif;
    font-size: 7.6px; line-height: 9.8px; color: var(--ink-dark); }
  .services .sep { display: inline-block; width: 3px; height: 3px; border-radius: 50%; background: var(--ink-dark); margin: 0 5px; vertical-align: middle; }
  .badge { position: absolute; top: 586px; width: 30px; height: 30px; border-radius: 50%; }
  .badge.first { left: 427px; left: 335px; background: #e9ecf4; border: 2px solid #2c4a9a; }
  .badge.second { left: 378px; background: #d9b43a; border: 2px solid #1d3a7a; }

  .watermark { position: absolute; border-radius: 50%; background: var(--faint); opacity: .7; }
  .letterhead .watermark { left: 134px; top: 300px; width: 190px; height: 190px; }

  .envelope-back { left: 644px; top: 331px; width: 508px; height: 251px; }
  .envelope-back .brand-dot { position: absolute; left: 247px; top: 30px; }

  .envelope-front { left: 584px; top: 455px; width: 510px; height: 251px; }
  .envelope-front .brand { left: 31px; top: 26px; }
  .return-address { position: absolute; left: 62px; top: 49px; font-family: "Libre Caslon Text", Georgia, serif;
    color: #fff; font-size: 7.6px; line-height: 9.6px; }
  .envelope-front .watermark { left: 428px; top: 115px; width: 72px; height: 72px; }
</style>
</head>
<body>

<section class="sheet letterhead">
  <svg class="art" viewBox="0 0 761 1072" preserveAspectRatio="none" aria-hidden="true">
    <rect width="761" height="260" fill="var(--navy)"/>
    <path d="M0 185 C140 140 300 116 440 112 L440 140 L0 260 Z" fill="var(--gold)"/>
    <path d="M0 222 C150 160 300 122 440 116 C570 110 680 145 761 188 V1072 H0 Z" fill="#dfe2e8"/>
    <path d="M0 226 C150 166 300 128 440 122 C570 118 680 150 761 194 V1072 H0 Z" fill="var(--paper)"/>
  </svg>

  <div class="brand"><span class="brand-dot"></span>Harbor Law</div>

  <div class="contact">
    <div>48 Quay Lane</div>
    <div>Portside, Florida 30010</div>
    <div class="gap"></div>
    <div class="row"><svg viewBox="0 0 10 10"><path d="M2 0h2l1 3-1.5 1a6 6 0 0 0 2.5 2.5L7 5l3 1v2a2 2 0 0 1-2 2A8 8 0 0 1 0 2a2 2 0 0 1 2-2z"/></svg>(555)010-2746</div>
    <div class="row"><svg viewBox="0 0 10 10"><path d="M0 2h10v6H0z M0 2l5 3.5L10 2" stroke="var(--navy)" stroke-width=".8"/></svg>ned@harborlawgroup.example</div>
    <div class="row"><svg viewBox="0 0 10 10"><circle cx="5" cy="5" r="4.5"/></svg>www.harborlawgroup.example</div>
  </div>

  <div class="watermark"></div>

  <div class="letter">
    <p class="salutation">Dear Mr. Lane,</p>
    <p class="body">Lorem ipsum dolor sit amet, consectetur adipiscing elit. Donec orci purus, luctus vitae dignissim eu, iaculis sed purus. Vivamus faucibus, ipsum nec aliquet viverra, leo mauris condimentum ligula, sit amet sagittis enim ligula quis arcu. Nam egestas tortor id nisi porttitor mattis. In tortor ante, ultricies in suscipit a, tempus non massa. Vivamus et auctor mi. Fusce vel massa nulla. Phasellus nec eros mauris, et scelerisque orci.</p>
    <p class="body">Donec malesuada orci vitae nulla accumsan porta a id massa. Quisque accumsan iaculis magna sit amet fringilla. Maecenas consequat, magna eget tincidunt semper, odio nibh rutrum mi, id feugiat ante nisi eu risus. Vestibulum nunc orci, rhoncus a placerat in, ultricies in mi. Cras mattis varius eros, vel fringilla nisi suscipit eget. Quisque scelerisque sagittis nulla at porttitor.</p>
    <p class="body">Sed id augue vitae urna euismod commodo aliquet a quam. Pellentesque arcu velit, cursus et malesuada ut, consequat et diam. Nullam erat sem, rhoncus id ullamcorper vitae, rhoncus et arcu. In ultricies ultricies nulla, ut rutrum nisi iaculis at. Donec eu magna a metus ornare faucibus. Fusce aliquet faucibus ultricies. Morbi semper, est id tincidunt gravida, sem arcu adipiscing lacus, ac bibendum nulla leo eu purus. Quisque nec diam sed risus consectetur a ccumsan quis quis nibh. Vestibulum id purus lorem.</p>
  </div>

  <p class="closing">Sincerely,</p>
  <div class="signature" role="img" aria-label="Handwritten signature"></div>

  <div class="services">
    <div>Personal Injury<span class="sep"></span>Injunctions</div>
    <div>Criminal Defense<span class="sep"></span>Family Law</div>
  </div>
  <div class="badge first"></div>
  <div class="badge second"></div>
</section>

<section class="sheet envelope-back">
  <svg class="art" viewBox="0 0 508 251" preserveAspectRatio="none" aria-hidden="true">
    <path d="M0 0 H508 L490 50 Q482 81 452 81 H56 Q26 81 18 50 Z" fill="var(--navy)"/>
  </svg>
  <span class="brand-dot"></span>
</section>

<section class="sheet envelope-front">
  <svg class="art" viewBox="0 0 850 419" preserveAspectRatio="none" aria-hidden="true">
    <rect width="850" height="260" fill="var(--navy)"/>
    <path d="M0 182 C150 150 330 128 490 126 L490 150 L0 250 Z" fill="var(--gold)"/>
    <path d="M0 204 C170 152 340 130 490 130 C640 130 760 165 850 210 V419 H0 Z" fill="#dfe2e8"/>
    <path d="M0 210 C170 158 340 136 490 136 C640 136 760 170 850 216 V419 H0 Z" fill="var(--paper)"/>
  </svg>
  <div class="brand"><span class="brand-dot"></span>Harbor Law</div>
  <div class="return-address">
    <div>48 Quay Lane</div>
    <div>Portside, Florida 30010</div>
  </div>
  <div class="watermark"></div>
</section>

</body>
</html>
```